Interior Design Company - Project Folder Design

Require simple layout design for company folders in a specific template as attach. Company name is MORVEL. Tag line is "make each space your own story" in Microsoft Word <Juice ITC> font type. Corporate colors include dark grey, turqoise and white.
Logo, AI template and some images are attached.

Company focus on Interior Design and Build services. Our services includes all commercial and residential projects.

Target Market(s)

B2B,B2C Corporate and Residential Design, Fit-outs and Project Management

Industry/Entity Type

Interior

Font styles to use
Sans Serif

Colors
33a6d7
333333
ffffff

Requirements
Must have
• Logo
• Address - No. 58 Kelton Road #03-21, Varlow Plaza, Singapore 179452
• Web - www.morvel-example.com
Nice to have
• Clean professional architectural lines
Should not have
• No cartoons, kiddy images nor repetitive patterns

```html
<!DOCTYPE html>
<html lang="en">
<head>
<meta charset="utf-8">
<title>MORVEL – Project Folder Dieline</title>
<link rel="stylesheet" href="https://fonts.googleapis.com/css2?family=Josefin+Sans:wght@300;400&display=swap">
<style>
  :root {
    --backdrop: #0b2526;
    --backdrop-glow: #12403f;
    --panel: #4a4a4c;
    --panel-dark: #3b3b3d;
    --panel-edge: #2c2c2e;
    --line-grey: #8a8a8c;
    --turquoise: #33a6d7;
    --white: #ffffff;
    --text-soft: #d9d9d9;
  }
  * { margin: 0; padding: 0; box-sizing: border-box; }
  html, body {
    width: 1200px; height: 798px; overflow: hidden;
    background: radial-gradient(ellipse at 50% 30%, var(--backdrop-glow) 0%, var(--backdrop) 70%);
    font-family: "Josefin Sans", sans-serif;
  }
  .folder-dieline {
    position: absolute; left: 64px; top: 83px;
    width: 1073px; height: 632px;
  }
  .folder-dieline svg { position: absolute; inset: 0; }
  .brand-name {
    position: absolute; transform: translateX(-50%);
    font-weight: 300; color: var(--white); letter-spacing: 1px;
    line-height: 1; white-space: nowrap;
  }
  .brand-name--flap { left: 105px; top: 96px; font-size: 30px; }
  .brand-name--cover { left: 910px; top: 98px; font-size: 40px; }
  .brand-mark {
    display: inline-block; width: 6px; height: 6px; margin-left: 6px;
    background: var(--turquoise); vertical-align: middle;
  }
  .flap-address {
    position: absolute; left: 105px; top: 195px; transform: translateX(-50%);
    width: 180px; text-align: center;
    font-size: 9px; line-height: 1.45; color: var(--text-soft); font-weight: 300;
  }
  .inner-address {
    position: absolute; left: 306px; top: 542px;
    font-size: 16px; line-height: 1.35; color: var(--text-soft); font-weight: 300;
  }
  .cover-web {
    position: absolute; left: 873px; top: 576px; transform: translateX(-50%);
    font-size: 13px; color: var(--text-soft); font-weight: 300; white-space: nowrap;
  }
</style>
</head>
<body>
  <div class="folder-dieline">
    <svg width="1073" height="632" viewBox="0 0 1073 632" aria-hidden="false">
      <defs>
        <linearGradient id="line-art-grey" x1="0" y1="0" x2="1" y2="1">
          <stop offset="0" stop-color="#6a6a6c" stop-opacity="0.55"/>
          <stop offset="1" stop-color="#5a5a5c" stop-opacity="0.25"/>
        </linearGradient>
        <linearGradient id="line-art-turquoise" x1="0" y1="0" x2="1" y2="0">
          <stop offset="0" stop-color="#5d7f86" stop-opacity="0.6"/>
          <stop offset="1" stop-color="#5a5a5c" stop-opacity="0.4"/>
        </linearGradient>
      </defs>

      <!-- pocket flap with tabs -->
      <polygon class="flap-tab" points="0,32 10,0 200,0 210,32" fill="var(--panel)"/>
      <rect class="flap-tab-band" x="0" y="32" width="210" height="14" fill="var(--panel-dark)"/>
      <rect class="flap-panel" x="0" y="46" width="210" height="522" fill="var(--panel)"/>
      <rect class="flap-bottom-band" x="0" y="568" width="210" height="14" fill="var(--panel-dark)"/>
      <rect class="flap-bottom-tab" x="0" y="582" width="210" height="24" fill="var(--panel)"/>
      <g role="img" aria-label="Architectural line artwork across the pocket flap">
        <polygon points="0,500 0,430 140,340 210,290 210,370 120,420" fill="url(#line-art-grey)"/>
      </g>
      <g class="card-slot" fill="none" stroke="var(--panel-edge)" stroke-width="1.5">
        <path d="M20,470 q10,20 0,40"/>
        <path d="M110,465 q-14,22 0,44"/>
        <path d="M190,465 q-14,22 0,44"/>
        <path d="M70,552 q40,-30 80,0"/>
      </g>

      <!-- fold line -->
      <rect x="210" y="32" width="5" height="568" fill="var(--panel-edge)"/>

      <!-- inside panel -->
      <rect class="inner-panel" x="215" y="32" width="420" height="568" fill="var(--panel)"/>
      <g role="img" aria-label="Architectural line artwork across the top of the inside panel">
        <polygon points="215,90 330,50 420,32 635,32 635,55 470,120 300,170 215,190" fill="url(#line-art-turquoise)"/>
      </g>

      <!-- spine -->
      <rect class="spine" x="635" y="32" width="25" height="568" fill="var(--panel-dark)"/>
      <line x1="635" y1="32" x2="635" y2="600" stroke="var(--panel-edge)"/>
      <line x1="660" y1="32" x2="660" y2="600" stroke="var(--panel-edge)"/>

      <!-- front cover -->
      <rect class="cover-panel" x="660" y="32" width="413" height="568" fill="var(--panel)"/>
      <g role="img" aria-label="Architectural diagonal line artwork on the front cover">
        <polygon points="660,60 800,140 860,250 800,330 660,330" fill="url(#line-art-turquoise)"/>
        <polygon points="1073,100 1073,310 880,540 710,600 660,600 660,520 900,330" fill="url(#line-art-grey)"/>
      </g>
    </svg>

    <div class="brand-name brand-name--flap">morvel<span class="brand-mark"></span></div>
    <p class="flap-address">No. 58 Kelton Road #03-21,<br>Varlow Plaza, Singapore 179452</p>

    <p class="inner-address">No. 58 Kelton Road #03-21,<br>Varlow Plaza, Singapore 179452</p>

    <div class="brand-name brand-name--cover">morvel<span class="brand-mark"></span></div>
    <p class="cover-web">www.morvel-example.com</p>
  </div>
</body>
</html>
```